Brightfen Business Card Redesign & Logo Update

We need to update our business cards to something more modern and fresh. Brightfen can provide the current color schemes and old design examples, but welcome creativity in helping us with this redesign. PLEASE NOTE that we no longer utilize the "tree" and/or "leaf" imagery in our branding. If able would apprecaite an update on the quality of our "words only" logo in Ai. / PNG formats too.

Target Market(s)

Investors, landowners, corporate partners, contractors

Industry/Entity Type

Environmental Restoration & Conservation

Contact Information for Business Card

Logo, persons name, title, mailing address, phone and email, website url

Font styles to use
Other font styles liked:
• Merriweather

Requirements
Nice to have
• Logo, persons name, title, mailing address, phone and email, website url, but open to ideams
Should not have
• No all back backgrounds

```html
<!DOCTYPE html>
<html lang="en">
<head>
<meta charset="utf-8">
<title>Brightfen Business Card</title>
<link href="https://fonts.googleapis.com/css2?family=Merriweather:wght@400;700;900&display=swap" rel="stylesheet">
<style>
  :root {
    --green: #177d3f;
    --orange: #ec7d22;
    --ink: #1d1d1d;
    --paper: #ffffff;
    --backdrop: #e6e7e6;
  }
  * { margin: 0; padding: 0; box-sizing: border-box; }
  html, body { width: 1200px; height: 1000px; overflow: hidden; }
  body {
    background: var(--backdrop);
    font-family: "Merriweather", Georgia, serif;
    color: var(--ink);
  }
  .card {
    position: absolute;
    left: 250px;
    width: 700px;
    height: 400px;
    background: var(--paper);
    overflow: hidden;
    box-shadow: 0 6px 20px rgba(0,0,0,0.15);
  }
  .card-front { top: 70px; }
  .card-back { top: 530px; }

  .wordmark { position: absolute; text-align: left; }
  .wordmark-name {
    display: block;
    font-weight: 900;
    color: var(--green);
    letter-spacing: 1px;
    line-height: 1;
  }
  .wordmark-tagline {
    display: block;
    font-weight: 700;
    text-transform: uppercase;
    color: var(--ink);
    letter-spacing: 0.5px;
  }
  .card-front .wordmark { right: 40px; top: 40px; }
  .card-front .wordmark-name { font-size: 44px; }
  .card-front .wordmark-tagline { font-size: 10.5px; margin-top: 6px; }

  .rule {
    position: absolute;
    left: 250px; right: 40px; top: 150px;
    height: 2px;
    background: var(--orange);
  }

  .person { position: absolute; left: 40px; top: 150px; }
  .person-name { font-size: 22px; font-weight: 700; letter-spacing: 0.5px; }
  .person-name .first { color: var(--orange); }
  .person-name .last { color: var(--green); }
  .person-title { font-size: 15px; margin-top: 4px; }

  .contact { position: absolute; left: 40px; top: 222px; list-style: none; }
  .contact li {
    display: flex; align-items: center; gap: 8px;
    font-size: 14px; line-height: 22px;
  }
  .contact svg { width: 14px; height: 14px; flex: none; }

  .address {
    position: absolute; right: 40px; top: 205px;
    font-size: 14px; line-height: 22px; text-align: right;
    font-style: normal;
  }

  .bands { position: absolute; left: 0; bottom: 0; width: 700px; height: 120px; }

  .card-back .mark-group {
    position: absolute; left: 50%; top: 50%;
    transform: translate(-50%, -50%);
    display: flex; align-items: center; gap: 22px;
  }
  .mark-dot {
    width: 70px; height: 70px; border-radius: 50%;
    background: var(--orange);
    flex: none;
  }
  .card-back .wordmark { position: static; }
  .card-back .wordmark-name { font-size: 58px; }
  .card-back .wordmark-tagline { font-size: 13.5px; margin-top: 8px; }
</style>
</head>
<body>

<section class="card card-front" aria-label="Business card front">
  <div class="wordmark">
    <span class="wordmark-name">BRIGHTFEN</span>
    <span class="wordmark-tagline">Environmental Credit Company</span>
  </div>
  <div class="rule"></div>

  <div class="person">
    <p class="person-name"><span class="first">MAREN</span> <span class="last">HOLT</span></p>
    <p class="person-title">Founder</p>
  </div>

  <ul class="contact">
    <li>
      <svg viewBox="0 0 16 16" aria-hidden="true"><circle cx="8" cy="8" r="8" fill="var(--orange)"/><path d="M5 4.5c.6-.4 1.1-.3 1.4.2l.6 1.2c.2.4.1.8-.2 1l-.5.4c.4.9 1 1.5 1.9 1.9l.4-.5c.3-.3.6-.4 1-.2l1.2.6c.5.3.6.8.2 1.4-.6.8-1.6 1-2.6.5C6.9 10.3 5.7 9.1 5 7.6c-.5-1-.3-2.3 0-3.1z" fill="#fff"/></svg>
      (555) 210-4830
    </li>
    <li>
      <svg viewBox="0 0 16 16" aria-hidden="true"><circle cx="8" cy="8" r="8" fill="var(--orange)"/><rect x="4" y="5.2" width="8" height="5.6" fill="#fff"/><path d="M4 5.2l4 3 4-3" fill="none" stroke="var(--orange)" stroke-width="0.9"/></svg>
      maren@brightfen.org
    </li>
    <li>
      <svg viewBox="0 0 16 16" aria-hidden="true"><circle cx="8" cy="8" r="8" fill="var(--orange)"/><circle cx="8" cy="8" r="4" fill="none" stroke="#fff" stroke-width="1"/><ellipse cx="8" cy="8" rx="1.8" ry="4" fill="none" stroke="#fff" stroke-width="0.9"/><path d="M4 8h8" stroke="#fff" stroke-width="0.9"/></svg>
      www.brightfen.org
    </li>
  </ul>

  <address class="address">
    48 Marsh Lane, Suite 12<br>
    PO Box 3172, Fenwick
  </address>

  <svg class="bands" viewBox="0 0 700 120" aria-hidden="true">
    <polygon points="380,22 700,22 700,28 392,28" fill="var(--green)"/>
    <polygon points="410,38 700,38 700,100 470,100 440,70" fill="var(--orange)"/>
    <polygon points="0,70 380,70 420,120 0,120" fill="var(--green)"/>
    <polygon points="470,106 700,106 700,120 480,120" fill="var(--orange)"/>
  </svg>
</section>

<section class="card card-back" aria-label="Business card back">
  <div class="mark-group">
    <span class="mark-dot" aria-hidden="true"></span>
    <div class="wordmark">
      <span class="wordmark-name">BRIGHTFEN</span>
      <span class="wordmark-tagline">Environmental Credit Company</span>
    </div>
  </div>
</section>

</body>
</html>
```